Industrial Project Sign

We need an eye catching (but professional) industrial project sign that will be very large (roughly 12' high x 18' wide). This sign will be highly visible from the adjacent high speed highway.

* The following needs to be at the bottom of the signage: Logo (uploaded), Name (Brightline Property Partners, Inc.) (uploaded) and phone number (415)736-2958

*Name of Project - "Meridale Commerce Park"

* Text items
Land for Sale
Build to Suit
Zoning: Industrial (G I & L I)

* Interesting background that is eye catching
Updates

Good morning all,

We are considering all designers options as we go and are waiting for the final designs to come in by the 4th so that we can give each one a good look.   If you have any new designs, questions, further design options or any tweeks you want to do to current designs, please do so at this time.

Thanks to all of you for your submissions.

Industry/Entity Type

Industrial

```html
<!DOCTYPE html>
<html lang="en">
<head>
<meta charset="utf-8">
<title>Meridale Commerce Park – Land For Sale Sign</title>
<link rel="stylesheet" href="https://fonts.googleapis.com/css2?family=Anton&family=Arimo:wght@700&display=swap">
<style>
  :root {
    --sign-maroon: #3a0000;
    --sign-white: #ffffff;
    --page-bg: #ffffff;
  }
  html, body {
    margin: 0;
    padding: 0;
    width: 1200px;
    height: 1000px;
    overflow: hidden;
    background: var(--page-bg);
  }
  .canvas {
    position: relative;
    width: 1200px;
    height: 1000px;
  }
  .sign {
    position: absolute;
    left: 0;
    top: 0;
  }
  .headline {
    font-family: "Anton", "Oswald", sans-serif;
    fill: var(--sign-white);
  }
  .subline {
    font-family: "Arimo", Arial, sans-serif;
    font-weight: 700;
    fill: var(--sign-white);
  }
  .company-name,
  .phone {
    font-family: "Arimo", Arial, sans-serif;
    font-weight: 700;
    fill: var(--sign-maroon);
  }
</style>
</head>
<body>
<main class="canvas">
  <svg class="sign" width="1200" height="1000" viewBox="0 0 1200 1000" xmlns="http://www.w3.org/2000/svg">
    <rect class="board" x="331" y="320" width="538" height="360" fill="var(--sign-maroon)"/>

    <text class="subline project-name" x="382" y="358" font-size="28" textLength="436" lengthAdjust="spacingAndGlyphs">MERIDALE COMMERCE PARK</text>

    <text class="headline" x="382" y="430" font-size="68" textLength="436" lengthAdjust="spacingAndGlyphs">LAND FOR SALE</text>
    <text class="subline" x="455" y="466" font-size="28" textLength="290" lengthAdjust="spacingAndGlyphs">BUILD TO SUIT</text>
    <text class="subline" x="430" y="503" font-size="32" textLength="340" lengthAdjust="spacing">INDUSTRIAL</text>
    <text class="subline" x="470" y="535" font-size="24" textLength="260" lengthAdjust="spacingAndGlyphs">ZONING: G I &amp; L I</text>

    <ellipse class="badge-ring" cx="600" cy="580" rx="250" ry="31" fill="none" stroke="var(--sign-white)" stroke-width="2.5"/>
    <ellipse class="badge-field" cx="600" cy="580" rx="245" ry="27" fill="var(--sign-white)"/>
    <ellipse class="badge-inline" cx="600" cy="580" rx="241" ry="24" fill="none" stroke="var(--sign-maroon)" stroke-width="1.5"/>
    <rect class="company-mark" x="462" y="572" width="16" height="16" fill="var(--sign-maroon)"/>
    <text class="company-name" x="488" y="587" font-size="18" textLength="256" lengthAdjust="spacingAndGlyphs">Brightline Property Partners, Inc</text>

    <rect class="phone-band" x="333" y="614" width="534" height="59" fill="var(--sign-white)"/>
    <text class="phone" x="398" y="665" font-size="60" textLength="404" lengthAdjust="spacingAndGlyphs">415-736-2958</text>
  </svg>
</main>
</body>
</html>
```